Business Card: RW Office Partners - Your organised problem solver

Business Name: RW Office Partners
Website: www.rwofficepartners.com.au
Email: marisol@rwofficepartners.com.au
Mobile: 61 482 907 236
Facebook: @rwofficepartners
Instrgram: @rwofficepartners

Brading Colours:
HEX
#986474
#ddccd3
#7a8498
#c9d8e4
#000000
#ffffff

Tag Line: Your organised problem solver

Link to DRAFT website:
https://deskhelpcollective.wixsite.com/rw-office-partners

About Page from the website:
My name is Marisol Wrenfield, and I would love to assist you to become more productive in your day to day and achieve your business and personal goals.
My mission is to give you time, time to work on the important tasks of your business or to be able to spend more time with your family. I will take on the tasks you don’t have time for, don’t know well or simply don’t like to do.
I have an extensive background in Administration, Tender Coordination, Document Control, WHS and Quality Management working primarily in the Construction, Mining and Corporate World.
I am passionate about being organised, having order and making things in your life (and mine) easier! I love to watch something unfold and grow into something amazing! I am known for being the go-to problem solver, the organiser of all things, producing high standards of work even under pressure. I’m also a confident communicator, and I understand that you’re busy running your business.

Target Market(s)

Small to Medium Business who require assistance in their business by a virtual assistant.

Industry/Entity Type

Virtual Assistant

Contact Information for Business Card

Mobile: 61 482 907 236

Font styles to use
Sans Serif

Colors
ffffff

Requirements
Must have
• Branding Colours as outlined.
Contact Details as outlined.
Logo as provided.
Proper contact details - mobile, facebook, instragm, website.
Simple, Elegant, very clean looking.
Should not have
• Note cute with pictures.
Not too girly as still want to market to construction companies.

```html
<!DOCTYPE html>
<html lang="en">
<head>
<meta charset="utf-8">
<title>RW Office Partners – Business Card</title>
<link rel="stylesheet" href="https://fonts.googleapis.com/css2?family=Montserrat:wght@500;600;700&family=Roboto:wght@400&display=swap">
<style>
  :root {
    --mauve: #986474;
    --mauve-light: #ddccd3;
    --slate: #7a8498;
    --slate-light: #c9d8e4;
    --ink: #000000;
    --paper: #ffffff;
    --stage: #e9e7ea;
    --rule: #b9b9bf;
  }
  * { box-sizing: border-box; margin: 0; padding: 0; }
  html, body { width: 1200px; height: 1108px; overflow: hidden; }
  body {
    background: var(--stage);
    font-family: "Montserrat", sans-serif;
    position: relative;
  }
  .card {
    position: absolute;
    top: 244px;
    width: 380px;
    height: 620px;
    border-radius: 24px;
    overflow: hidden;
    box-shadow: 0 6px 18px rgba(0,0,0,0.12);
  }
  .card--front { left: 190px; background: var(--paper); text-align: center; }
  .card--back {
    left: 630px;
    background: linear-gradient(180deg, var(--slate) 0%, #8a7287 55%, var(--mauve) 100%);
  }

  /* Front */
  .brand {
    margin-top: 110px;
    font-weight: 700;
    color: var(--slate);
    font-size: 46px;
    line-height: 1.02;
    letter-spacing: 1px;
    text-transform: uppercase;
  }
  .person {
    margin-top: 70px;
    font-weight: 600;
    color: var(--mauve);
    font-size: 21px;
    letter-spacing: 0.5px;
    text-transform: uppercase;
  }
  .divider {
    display: flex;
    align-items: center;
    justify-content: center;
    gap: 8px;
    margin: 14px auto 10px;
    width: 250px;
  }
  .divider::before, .divider::after {
    content: "";
    flex: 1;
    height: 1px;
    background: var(--rule);
  }
  .icon-box {
    width: 24px; height: 24px;
    border-radius: 3px;
    background: var(--mauve);
    display: flex; align-items: center; justify-content: center;
  }
  .social-dot {
    width: 26px; height: 26px;
    border-radius: 50%;
    border: 1.5px solid var(--slate);
  }
  .contact {
    font-family: "Roboto", sans-serif;
    font-size: 17px;
    color: #222;
    line-height: 1.35;
  }
  .handle {
    font-family: "Roboto", sans-serif;
    font-size: 17px;
    color: #222;
  }

  /* Back */
  .back-mark {
    position: absolute;
    top: 395px; left: 0; right: 0;
    text-align: center;
    color: var(--paper);
    font-weight: 700;
    font-size: 20px;
    letter-spacing: 1px;
    text-transform: uppercase;
  }
  .tagline {
    position: absolute;
    top: 518px; left: 0; right: 0;
    text-align: center;
    color: var(--paper);
    font-weight: 600;
    font-size: 22px;
    line-height: 1.1;
    text-transform: uppercase;
  }
</style>
</head>
<body>
  <section class="card card--front">
    <h1 class="brand">RW Office<br>Partners</h1>
    <p class="person">Marisol Wrenfield</p>
    <div class="divider">
      <span class="icon-box">
        <svg width="14" height="14" viewBox="0 0 24 24" aria-hidden="true"><path fill="#fff" d="M6.6 10.8a15 15 0 0 0 6.6 6.6l2.2-2.2c.3-.3.7-.4 1-.2 1.1.4 2.3.6 3.6.6.6 0 1 .4 1 1V20c0 .6-.4 1-1 1A17 17 0 0 1 3 4c0-.6.4-1 1-1h3.5c.6 0 1 .4 1 1 0 1.3.2 2.5.6 3.6.1.3 0 .7-.2 1z"/></svg>
      </span>
      <span class="icon-box">
        <svg width="14" height="14" viewBox="0 0 24 24" aria-hidden="true"><rect x="2" y="5" width="20" height="14" rx="1.5" fill="#fff"/><path d="M3 6l9 7 9-7" stroke="#986474" stroke-width="2" fill="none"/></svg>
      </span>
      <span class="icon-box">
        <svg width="14" height="14" viewBox="0 0 24 24" aria-hidden="true"><path fill="#fff" d="M12 2a7 7 0 0 0-7 7c0 5 7 13 7 13s7-8 7-13a7 7 0 0 0-7-7zm0 9.5A2.5 2.5 0 1 1 12 6.5a2.5 2.5 0 0 1 0 5z"/></svg>
      </span>
    </div>
    <div class="contact">
      <p>61 482 907 236</p>
      <p>marisol@rwofficepartners.com.au</p>
      <p>www.rwofficepartners.com.au</p>
    </div>
    <div class="divider">
      <span class="social-dot"></span>
      <span class="social-dot"></span>
    </div>
    <p class="handle">@rwofficepartners</p>
  </section>

  <section class="card card--back" role="img" aria-label="Soft slate to mauve gradient card back">
    <p class="back-mark">RW Office Partners</p>
    <p class="tagline">Your organised<br>problem solver</p>
  </section>
</body>
</html>
```